Bramwell IT Services Business Card

Bramwell IT Services are a Perth based IT Services company. We would like to incorporate our company logo (attached) and stick with the blue that is in that design. I would like a clean look design that isn't too busy, yet creates a lasting image that is instantly recognisable in the recipients mind.

Target Market(s)

The target audience is small/medium business owners.

Industry/Entity Type

Business

Font styles to use
Serif
Sans Serif

Colors

Designer to choose colors to be used in the design.

Requirements
Must have
• The design should include:
Business name: Bramwell IT Services
Directors Name: Marcus Tenley
Phone Number: 0483 562 904
Email: support@bramwellit.com.au
Website: www.bramwellit.com.au

```html
<!DOCTYPE html>
<html lang="en">
<head>
<meta charset="utf-8">
<title>Bramwell IT Services Business Card</title>
<link href="https://fonts.googleapis.com/css2?family=Open+Sans:wght@400;600&display=swap" rel="stylesheet">
<style>
  :root {
    --brand-blue: #0b4fa8;
    --brand-blue-deep: #08418e;
    --brand-blue-light: #5d8fd6;
    --ink: #2b2b2b;
    --paper: #ffffff;
    --backdrop-top: #f4f4f4;
    --backdrop-bottom: #c9c9c9;
  }
  * { margin: 0; padding: 0; box-sizing: border-box; }
  html, body { width: 1200px; height: 873px; overflow: hidden; }
  body {
    background: linear-gradient(180deg, var(--backdrop-top) 0%, var(--backdrop-bottom) 100%);
    font-family: "Open Sans", Arial, sans-serif;
    display: flex;
    align-items: center;
    justify-content: center;
    gap: 40px;
  }
  .card {
    position: relative;
    width: 520px;
    height: 296px;
    overflow: hidden;
    box-shadow: 0 6px 18px rgba(0,0,0,0.28);
  }
  /* Front */
  .card-front {
    background: linear-gradient(135deg, var(--brand-blue) 0%, var(--brand-blue-deep) 100%);
  }
  .card-front .watermark {
    position: absolute;
    left: 30px; top: -40px;
    width: 300px; height: 300px;
    border-radius: 50%;
    background: radial-gradient(circle, rgba(255,255,255,0.10) 0%, rgba(255,255,255,0.02) 70%, rgba(255,255,255,0) 100%);
  }
  .brand {
    display: flex;
    align-items: center;
    gap: 8px;
    font-weight: 600;
    white-space: nowrap;
  }
  .brand-mark {
    width: 12px; height: 12px;
  }
  .card-front .brand {
    position: absolute;
    left: 50%; top: 50%;
    transform: translate(-50%, -50%);
    color: var(--paper);
    font-size: 24px;
  }
  .card-front .brand-mark { background: var(--paper); }

  /* Back */
  .card-back { background: var(--paper); }
  .card-back .brand {
    position: absolute;
    left: 44px; top: 44px;
    color: var(--brand-blue);
    font-size: 21px;
  }
  .card-back .brand-mark { background: var(--brand-blue); }
  .person {
    position: absolute;
    left: 90px; top: 124px;
  }
  .person-name {
    color: var(--brand-blue);
    font-size: 16px;
    font-weight: 400;
  }
  .person-role {
    color: var(--ink);
    font-size: 11px;
    margin-top: 1px;
  }
  .contacts {
    position: absolute;
    left: 90px; top: 186px;
    list-style: none;
    font-size: 12px;
    color: var(--ink);
  }
  .contacts li {
    display: flex;
    align-items: center;
    gap: 8px;
    height: 19px;
  }
  .contacts svg { width: 11px; height: 11px; fill: var(--brand-blue); }
  .card-back .watermark {
    position: absolute;
    right: 40px; top: 90px;
    width: 130px; height: 150px;
    border-radius: 50%;
    background: radial-gradient(circle, rgba(11,79,168,0.12) 0%, rgba(11,79,168,0.04) 70%, rgba(11,79,168,0) 100%);
  }
  .wave {
    position: absolute;
    left: 0; bottom: 0;
    width: 520px; height: 80px;
  }
</style>
</head>
<body>
  <section class="card card-front" aria-label="Business card front">
    <div class="watermark" role="img" aria-label="Faint brand watermark area"></div>
    <div class="brand"><span class="brand-mark"></span>Bramwell IT Services</div>
  </section>

  <section class="card card-back" aria-label="Business card back">
    <div class="watermark" role="img" aria-label="Faint brand watermark area"></div>
    <div class="brand"><span class="brand-mark"></span>Bramwell IT Services</div>
    <div class="person">
      <p class="person-name">Marcus Tenley</p>
      <p class="person-role">Director</p>
    </div>
    <ul class="contacts">
      <li><svg viewBox="0 0 12 12"><path d="M2 1h3l1 3-2 1c1 1.5 2 2.5 3 3l1-2 3 1v3c-5 1-11-5-9-9z"/></svg>0483 562 904</li>
      <li><svg viewBox="0 0 12 12"><path d="M0 2h12v8H0z M1 3l5 4 5-4" stroke="#fff" stroke-width="1"/></svg>support@bramwellit.com.au</li>
      <li><svg viewBox="0 0 12 12"><circle cx="6" cy="6" r="6"/><path d="M0 6h12M6 0v12M6 0c-3 3-3 9 0 12M6 0c3 3 3 9 0 12" stroke="#fff" stroke-width="0.8" fill="none"/></svg>www.bramwellit.com.au</li>
    </ul>
    <svg class="wave" viewBox="0 0 520 80" preserveAspectRatio="none" aria-hidden="true">
      <path d="M0 20 C120 22 240 40 320 58 C400 74 470 42 520 28 L520 80 L0 80 Z" fill="var(--brand-blue-light)"/>
      <path d="M0 26 C120 28 240 46 320 64 C400 80 470 48 520 34 L520 80 L0 80 Z" fill="var(--paper)"/>
      <path d="M0 29 C120 31 240 49 320 67 C400 83 470 51 520 37 L520 80 L0 80 Z" fill="var(--brand-blue)"/>
    </svg>
  </section>
</body>
</html>
```